Mobile Fitness snd Therapy Business Card Design

I need a business card designed for my mobile fitness and therapy business.

Please view the images that I have uploaded. I like the simplicity of the design that I have attached. I adapted it with my information

Target Market(s)

Those seeking personal training, injury rehabilitation or massage therapy.

Industry/Entity Type

Business

Contact Information for Business Card

Derek Fulham - MSc, CAT(C), RMT, CSCS, Pn2
e-mail: derek@vantrelo.com
website: www.vantrelo.com
instagram: @derek_fulham

Font styles to use
Sans Serif

Colors
3176b5
0355a3

Requirements
Must have
• "Contact us to receive a FREE assessment"
• Services offered:
• Personal Training
• Golf Fitness
• Injury Rehab
• Massage Therapy
• Yoga
Nice to have
• Consistent colours with brand
• - Dark Blue: #232837
• - Blue: #5096f0
• Consistent look/feel with the website: www.vantrelo.com

```html
<!DOCTYPE html>
<html lang="en">
<head>
<meta charset="UTF-8">
<title>Vantrelo Business Card</title>
<link href="https://fonts.googleapis.com/css2?family=Roboto:wght@400;500;700&family=Roboto+Condensed:wght@700&display=swap" rel="stylesheet">
<style>
  :root {
    --page-bg: #d9dcdf;
    --card-bg: #eef0f2;
    --card-edge: #ffffff;
    --ink-dark: #232837;
    --ink-body: #3a3d45;
    --brand-blue: #0355a3;
    --accent-blue: #1f47b5;
    --deco-light: #4f6f9c;
    --deco-deep: #1e3fb0;
  }
  html, body {
    margin: 0;
    padding: 0;
    width: 1200px;
    height: 969px;
    overflow: hidden;
    background: var(--page-bg);
  }
  .canvas {
    position: relative;
    width: 1200px;
    height: 969px;
  }
  .business-card {
    position: absolute;
    left: 100px;
    top: 199px;
    width: 1000px;
    height: 571px;
    border-radius: 34px;
    background: linear-gradient(160deg, #f6f7f8 0%, var(--card-bg) 60%, #e4e7ea 100%);
    box-shadow: 0 0 0 2px var(--card-edge) inset, 0 18px 40px rgba(35, 40, 55, 0.18);
    font-family: "Roboto", Arial, sans-serif;
    color: var(--ink-body);
    overflow: hidden;
  }
  .brand-decoration {
    position: absolute;
    left: 541px;
    top: 30px;
    width: 433px;
    height: 503px;
    border-radius: 40px;
    background: linear-gradient(100deg, var(--deco-light) 0%, #2a50a8 50%, var(--deco-deep) 100%);
    opacity: 0.85;
  }
  .brand {
    position: absolute;
    left: 60px;
    top: 50px;
  }
  .brand-name {
    font-weight: 500;
    font-size: 54px;
    line-height: 1;
    letter-spacing: 6px;
    color: var(--ink-dark);
  }
  .brand-tagline {
    margin-top: 14px;
    font-weight: 700;
    font-size: 19px;
    letter-spacing: 4.6px;
    color: var(--ink-dark);
  }
  .person {
    position: absolute;
    left: 60px;
    top: 170px;
  }
  .person-name {
    font-family: "Roboto Condensed", "Arial Narrow", sans-serif;
    font-weight: 700;
    font-size: 36px;
    line-height: 1;
    color: var(--accent-blue);
    text-transform: uppercase;
  }
  .person-credentials {
    margin-top: 8px;
    font-family: "Roboto Condensed", "Arial Narrow", sans-serif;
    font-weight: 700;
    font-size: 17px;
    color: var(--accent-blue);
  }
  .contact-list {
    position: absolute;
    left: 60px;
    top: 242px;
    margin: 0;
    padding: 0;
    list-style: none;
  }
  .contact-item {
    display: flex;
    align-items: center;
    height: 32px;
    font-size: 24px;
    color: var(--ink-body);
  }
  .contact-icon {
    width: 20px;
    height: 20px;
    margin-right: 14px;
    flex-shrink: 0;
  }
  .services {
    position: absolute;
    left: 60px;
    top: 362px;
  }
  .services-heading {
    margin: 0 0 10px;
    font-size: 25px;
    font-weight: 700;
    color: var(--ink-dark);
    text-transform: uppercase;
  }
  .services-line {
    margin: 0;
    font-size: 24px;
    line-height: 36px;
    color: var(--ink-body);
  }
  .call-to-action {
    position: absolute;
    left: 60px;
    top: 488px;
    margin: 0;
    font-size: 23px;
    font-weight: 700;
    color: var(--accent-blue);
  }
</style>
</head>
<body>
<div class="canvas">
  <section class="business-card">
    <div class="brand-decoration" role="img" aria-label="Large blue brand decoration area"></div>

    <header class="brand">
      <div class="brand-name">VANTRELO</div>
      <div class="brand-tagline">NUTRITION - FITNESS - HEALTH</div>
    </header>

    <div class="person">
      <div class="person-name">Derek Fulham</div>
      <div class="person-credentials">MSC, CAT(C), RMT, CSCS, PN2</div>
    </div>

    <ul class="contact-list">
      <li class="contact-item">
        <svg class="contact-icon" viewBox="0 0 20 20" aria-hidden="true">
          <rect x="2" y="4" width="16" height="12" rx="1.5" fill="var(--accent-blue)"/>
          <path d="M3 5.5 L10 11 L17 5.5" fill="none" stroke="#eef0f2" stroke-width="1.6"/>
        </svg>
        derek@vantrelo.com
      </li>
      <li class="contact-item">
        <svg class="contact-icon" viewBox="0 0 20 20" aria-hidden="true">
          <circle cx="10" cy="10" r="8" fill="var(--accent-blue)"/>
          <ellipse cx="10" cy="10" rx="3.4" ry="8" fill="none" stroke="#eef0f2" stroke-width="1.2"/>
          <line x1="2" y1="10" x2="18" y2="10" stroke="#eef0f2" stroke-width="1.2"/>
        </svg>
        www.vantrelo.com
      </li>
      <li class="contact-item">
        <svg class="contact-icon" viewBox="0 0 20 20" aria-hidden="true">
          <circle cx="10" cy="10" r="8" fill="var(--accent-blue)"/>
        </svg>
        @derek_fulham
      </li>
    </ul>

    <div class="services">
      <h2 class="services-heading">Services Offered:</h2>
      <p class="services-line">Personal Training | Golf Fitness</p>
      <p class="services-line">Injury Rehab | Massage Therapy | Yoga</p>
    </div>

    <p class="call-to-action">Contact us to receive a FREE assessment</p>
  </section>
</div>
</body>
</html>
```